Road Construction Company needs business cards

We would like a new business card designed for our business.

We're a road construction company based in Qld, Australia.

Can the business card please have the following information on it.

Name: Warren Halbeck
Position: General Manager
Phone: 0472 915 348
Email: Warren.halbeck@tovrin.com.au
Address: 87 Marrow Ave, Pendlebay, QLD, 4023
Website: www.tovrin.com.au

Visually we'd like the card to be professional and simple.

Attached is our logo.

Our website is www.tovrin.com.au

Target Market(s)

Men aged 25-60

Contact Information for Business Card

As listed in project description

Font styles to use
Serif

Requirements
Must have
• Large logo on back of card

```html
<!DOCTYPE html>
<html lang="en">
<head>
<meta charset="utf-8">
<title>Tovrin Business Card</title>
<link rel="stylesheet" href="https://fonts.googleapis.com/css2?family=Open+Sans:wght@400;600;700;800&display=swap">
<style>
  :root {
    --royal-blue: #1656a6;
    --sky-blue: #45a9dc;
    --white: #ffffff;
    --ink: #1a1a1a;
    --backdrop: #e6e8ec;
  }
  * { box-sizing: border-box; margin: 0; padding: 0; }
  html, body {
    width: 1200px;
    height: 780px;
    overflow: hidden;
    background: var(--backdrop);
    font-family: "Open Sans", Arial, sans-serif;
  }
  .canvas {
    position: relative;
    width: 1200px;
    height: 780px;
  }
  .card {
    position: absolute;
    width: 600px;
    height: 345px;
    border-radius: 26px;
    overflow: hidden;
    box-shadow: 0 10px 28px rgba(0, 0, 0, 0.18);
  }
  .card-back {
    left: 110px;
    top: 30px;
    background: var(--royal-blue);
    display: flex;
    align-items: center;
    justify-content: center;
  }
  .card-front {
    left: 490px;
    top: 405px;
    background: var(--white);
  }
  .wordmark {
    display: flex;
    align-items: center;
    gap: 14px;
    font-weight: 800;
    letter-spacing: 0.04em;
    line-height: 1;
  }
  .wordmark-mark {
    display: block;
    background: var(--sky-blue);
  }
  .card-back .wordmark { font-size: 92px; color: var(--white); }
  .card-back .wordmark-mark { width: 26px; height: 26px; }
  .front-graphics {
    position: absolute;
    inset: 0;
    width: 100%;
    height: 100%;
  }
  .identity {
    position: absolute;
    top: 34px;
    right: 62px;
    text-align: right;
  }
  .identity-name {
    font-size: 27px;
    font-weight: 700;
    color: var(--royal-blue);
    line-height: 1.1;
  }
  .identity-role {
    font-size: 13px;
    font-weight: 600;
    color: var(--ink);
    margin-top: 3px;
  }
  .card-front .wordmark {
    position: absolute;
    left: 38px;
    top: 132px;
    font-size: 44px;
    color: var(--royal-blue);
    gap: 10px;
  }
  .card-front .wordmark-mark { width: 13px; height: 13px; }
  .address {
    position: absolute;
    left: 40px;
    top: 200px;
    font-size: 14px;
    line-height: 1.35;
    color: var(--ink);
  }
  .contact-list {
    position: absolute;
    left: 40px;
    top: 246px;
    list-style: none;
    font-size: 14px;
    line-height: 1.4;
    color: var(--ink);
  }
  .contact-list li {
    display: flex;
    align-items: center;
    gap: 8px;
  }
  .contact-icon { width: 13px; height: 13px; flex: none; }
</style>
</head>
<body>
<main class="canvas">

  <section class="card card-back" aria-label="Business card back">
    <div class="wordmark"><span class="wordmark-mark"></span><span>TOVRIN</span></div>
  </section>

  <section class="card card-front" aria-label="Business card front">
    <svg class="front-graphics" viewBox="0 0 600 345" preserveAspectRatio="none" aria-hidden="true">
      <rect x="556" y="0" width="44" height="40" fill="var(--royal-blue)"/>
      <path d="M 200 345 C 380 330 480 235 600 105 L 600 345 Z" fill="var(--royal-blue)"/>
      <path d="M 120 316 C 300 322 420 265 510 190 C 430 275 310 334 140 330 Z" fill="var(--sky-blue)"/>
    </svg>

    <div class="identity">
      <p class="identity-name">Warren Halbeck</p>
      <p class="identity-role">General Manager</p>
    </div>

    <div class="wordmark"><span class="wordmark-mark"></span><span>TOVRIN</span></div>

    <p class="address">87 Marrow Ave,<br>Pendlebay, QLD, 4023</p>

    <ul class="contact-list">
      <li>
        <svg class="contact-icon" viewBox="0 0 16 16" aria-hidden="true"><circle cx="8" cy="8" r="8" fill="var(--sky-blue)"/><path d="M5 4.5 L6.6 4.2 L7.3 6 L6.4 6.8 Q7.2 8.7 9.2 9.6 L10 8.7 L11.8 9.4 L11.5 11 Q7.8 11.4 5.2 8 Q4.4 6 5 4.5 Z" fill="var(--white)"/></svg>
        <span>0472 915 348</span>
      </li>
      <li>
        <svg class="contact-icon" viewBox="0 0 16 16" aria-hidden="true"><circle cx="8" cy="8" r="8" fill="var(--sky-blue)"/><circle cx="8" cy="8" r="4.6" fill="none" stroke="var(--white)" stroke-width="1"/><path d="M3.4 8 H12.6 M8 3.4 V12.6" stroke="var(--white)" stroke-width="1"/></svg>
        <span>www.tovrin.com.au</span>
      </li>
      <li>
        <svg class="contact-icon" viewBox="0 0 16 16" aria-hidden="true"><circle cx="8" cy="8" r="8" fill="var(--sky-blue)"/><rect x="4" y="5" width="8" height="6" fill="var(--white)"/><path d="M4 5 L8 8.4 L12 5" fill="none" stroke="var(--sky-blue)" stroke-width="1"/></svg>
        <span>Warren.halbeck@tovrin.com.au</span>
      </li>
    </ul>
  </section>

</main>
</body>
</html>
```